A layout of a webpage for oil trade platform

I would like to have a desgin of one page webpage (with section scrollling dowin) that woulf present the new product i.e. oil trade platform for wholesale buyers and sellers.
Layout should consist of the sections similar to the given at: https://porada.leczmypol.pl/panel-planowania-spotkan
However oil industy require more colors and more photo stories than here for doctor.
I. I woul imagine at first below menu a slider with brueg information about the product and its advantages with "more" button next to the prict screen of our platform on different displays (PC and mobile).
II. Bellow the slider I would imagine icons correspoing to the advantages of that plaftorm:
1. Purchase/sale process automation 24/7
2. Access to the best deals
3. Electronic offerings and orderings
4. Transaction status monitoring
5. Data and transaction security
II A) (optional):
In near future we would like to prepare a short video presenation. Hence please prepare a place to display that element here.
At the moment alternatvily please prepare a How it works section that would explan the platform operating process
III. Next secion is about benefits for Oil Purchaser
It can be done either by icons of by text and corresponding grahip for while section.
Benefits:
- Access to cheaper oil
- Convenience of online orders
- Possibility to compare prices on the market
- Transaction history
- Order status monitoring
- Seccurity and transparency of purchase
IV. Next seciont is about benefits for Oil Seller
Benefits:
- New sale channel
- Attracting new clients
- More oil sold
- Transaction security
- Possibility to integrate with distribution infrastructure and logistits for more efficient automation.
V. Contact form
VI. Footer
I would need a layout that that will correspond to the very dynamic logo but I would expect also a clean form, smoth and modern. It has to be proffessional layout with more corporate character.
It can use a paralax features if needed.

```html
<!DOCTYPE html>
<html lang="en">
<head>
<meta charset="utf-8">
<title>Oilvane — Oil Trade Platform</title>
<link href="https://fonts.googleapis.com/css2?family=Lato:wght@400;700;900&display=swap" rel="stylesheet">
<style>
:root{
  --navy:#1c356b;
  --navy-dark:#142a58;
  --ink:#1f2a44;
  --icon:#2c4c8c;
  --orange:#f15a24;
  --orange-light:#f47a3a;
  --text:#6f6f6f;
  --muted:#8a8a8a;
  --light:#f5f5f5;
  --line:#dedede;
  --white:#ffffff;
}
*{box-sizing:border-box;margin:0;padding:0}
html,body{width:1200px;height:3285px;overflow:hidden}
body{font-family:"Lato",sans-serif;color:var(--text);background:var(--white);position:relative}
section,footer{position:absolute;left:0;width:1200px}
.abs{position:absolute}

/* hero */
.hero{top:0;height:668px;background:radial-gradient(ellipse at 30% 60%,#27468a 0%,var(--navy) 45%,var(--navy-dark) 100%);overflow:hidden}
.brand{display:flex;align-items:center;gap:12px;color:var(--white);font-weight:900;font-size:30px;letter-spacing:.5px}
.brand-dot{width:34px;height:34px;border-radius:50%;background:var(--orange)}
.hero .brand{left:77px;top:30px}
.nav{left:414px;top:45px;display:flex;gap:0}
.nav a{color:var(--white);text-decoration:none;font-size:13px;font-weight:700;padding:9px 17px;letter-spacing:.3px}
.nav a.active{background:var(--orange)}
.hero-title{left:75px;top:252px;width:480px;color:var(--white);font-size:33px;font-weight:700;line-height:42px}
.hero-text{left:75px;top:345px;width:440px;color:#dfe6f4;font-size:18px;line-height:28px}
.btn{display:flex;align-items:center;justify-content:center;gap:10px;color:var(--white);font-weight:700;font-size:14px;letter-spacing:.5px;background:linear-gradient(180deg,var(--orange-light),var(--orange));text-decoration:none}
.hero .btn{left:75px;top:458px;width:153px;height:50px;font-size:17px}

.screen{background:var(--white);position:absolute;overflow:hidden}
.screen .side{position:absolute;left:0;top:0;bottom:0;background:#2e3440}
.row{height:8px;background:#e9ecf1;margin:0 0 10px}
.row b{display:inline-block;height:8px;width:18px;background:#63b543;float:right}

/* features */
.features{top:668px;height:193px;background:var(--white)}
.feature{position:absolute;top:34px;width:220px;text-align:center;color:#3a3a3a;font-size:15px;line-height:22px;font-weight:700}
.feature svg{display:block;margin:0 auto 14px}

/* how */
.how{top:861px;height:427px;background:var(--light)}
.tablet{left:74px;top:43px;width:484px;height:340px;background:#2b303a;border-radius:12px}
.how h2,.benefits h2,.contact h2{color:var(--ink);font-size:27px;font-weight:700}
.how h2{position:absolute;left:613px;top:85px}
.how p{position:absolute;left:613px;top:140px;width:510px;font-size:13.5px;line-height:25px;color:var(--muted)}
.how .btn{left:613px;top:284px;width:241px;height:54px}

/* benefits */
.benefits{height:528px}
.purchaser{top:1288px;background:var(--white)}
.seller{top:1815px;background:var(--light)}
.photo{position:absolute;top:0;height:528px}
.benefit-list{position:absolute;list-style:none}
.benefit-list li{display:flex;align-items:flex-start;gap:40px;color:#3f3f3f;font-weight:700;font-size:14.5px;line-height:24px;margin-bottom:36px}
.seller .benefit-list li{gap:36px}
.benefit-list svg{flex:none}

/* contact */
.contact{top:2343px;height:504px;background:var(--white);text-align:center}
.contact h2{position:absolute;left:0;right:0;top:84px}
.contact .sub{position:absolute;left:0;right:0;top:138px;font-size:14px;color:#555}
.field{position:absolute;border:1px solid var(--line);background:var(--white);text-align:left;font-size:13px;color:#555;padding:14px 14px}
.contact .btn{left:480px;top:386px;width:240px;height:54px}

/* footer */
.footer{top:2847px;height:438px;background:var(--light)}
.footer .brand{left:79px;top:72px;color:var(--ink);font-size:28px}
.footer h4{color:var(--ink);font-size:14px;font-weight:900;letter-spacing:.3px;margin-bottom:14px}
.footer ul{list-style:none}
.footer li{font-size:14px;line-height:30.5px;color:#555}
.address{left:79px;top:145px;font-size:14px;line-height:26px;color:#555}
.contact-line{display:flex;align-items:center;gap:16px;color:var(--orange);font-size:14px}
.socials{left:79px;top:290px;display:flex;gap:16px}
.socials span{width:16px;height:16px;border-radius:50%;background:#9aa0a8}
.newsletter-input{width:243px;height:44px;border:1px solid var(--line);background:var(--white);font-size:13px;color:#555;padding:13px 10px}
.footer .btn{width:90px;height:40px;margin:14px 0 0 153px;font-size:14px}
.divider{left:79px;right:79px;top:340px;height:1px;background:var(--line)}
.copyright{left:0;right:0;top:384px;text-align:center;font-size:12px;color:var(--muted)}
</style>
</head>
<body>

<section class="hero">
  <div class="abs brand"><span class="brand-dot"></span>Oilvane</div>
  <nav class="abs nav">
    <a class="active" href="#">HOME</a><a href="#">ABOUT US</a><a href="#">SERVICES</a><a href="#">HOW IT WORKS</a><a href="#">BENEFITS</a><a href="#">BLOG</a><a href="#">CONTACT US</a>
  </nav>
  <h1 class="abs hero-title">Nam fermentum vestibulum amet turpis tincidunt.</h1>
  <p class="abs hero-text">Aliquam molestie, mi et imperdiet euismod, dui purus auctor tellus, et interdum lacus lectus et ante dignissim lectus vitae.</p>
  <a class="abs btn" href="#">MORE <svg width="10" height="14" viewBox="0 0 10 14"><path d="M2 1l6 6-6 6" stroke="#fff" stroke-width="2.5" fill="none"/></svg></a>

  <!-- desktop -->
  <div class="abs" style="left:580px;top:182px;width:613px;height:378px;background:#0d0d0d;border-radius:10px"></div>
  <div class="screen" style="left:594px;top:196px;width:585px;height:332px">
    <div class="side" style="width:86px"><div style="width:44px;height:44px;border-radius:50%;background:#c9ccd2;margin:18px auto"></div></div>
    <div style="position:absolute;left:100px;top:12px;font-size:12px;color:#333">My orders</div>
    <div style="position:absolute;left:100px;top:50px;right:16px">
      <div class="row" style="background:#d6dbe4"></div><div class="row"><b></b></div><div class="row"><b></b></div><div class="row"><b></b></div><div class="row"><b></b></div><div class="row"><b></b></div><div class="row"><b></b></div><div class="row"><b></b></div>
    </div>
  </div>
  <div class="abs" style="left:838px;top:560px;width:100px;height:80px;background:#111"></div>
  <div class="abs" style="left:780px;top:640px;width:220px;height:14px;background:#111;border-radius:3px"></div>
  <!-- laptop -->
  <div class="abs" style="left:449px;top:431px;width:372px;height:225px;background:#151515;border-radius:10px 10px 0 0"></div>
  <div class="screen" style="left:461px;top:443px;width:348px;height:203px">
    <div class="side" style="width:50px"><div style="width:26px;height:26px;border-radius:50%;background:#c9ccd2;margin:10px auto"></div></div>
    <div style="position:absolute;left:62px;top:40px;right:12px"><div class="row"><b></b></div><div class="row"><b></b></div><div class="row"><b></b></div><div class="row"><b></b></div><div class="row"><b></b></div></div>
  </div>
  <div class="abs" style="left:420px;top:656px;width:430px;height:12px;background:#cfd3d8;border-radius:0 0 10px 10px"></div>
  <!-- phone -->
  <div class="abs" style="left:1069px;top:427px;width:72px;height:230px;background:#111;border-radius:12px"></div>
  <div class="screen" style="left:1074px;top:455px;width:62px;height:175px;padding:20px 6px"><div class="row"></div><div class="row"></div><div class="row"></div><div class="row"></div><div class="row"></div></div>
</section>

<section class="features">
  <div class="feature" style="left:70px">
    <svg width="58" height="58" viewBox="0 0 58 58" fill="none" stroke="var(--icon)" stroke-width="2.5"><circle cx="29" cy="29" r="26"/><circle cx="29" cy="29" r="16"/><path d="M29 20v9h7"/></svg>
    Purchase/sale process<br>automation 24/7</div>
  <div class="feature" style="left:278px">
    <svg width="58" height="58" viewBox="0 0 58 58" fill="none" stroke="var(--icon)" stroke-width="2.5"><path d="M8 26h10v26H8zM18 28l10-18c4 0 6 3 5 7l-2 8h16c3 0 5 3 4 6l-4 16c-1 3-3 4-6 4H18"/></svg>
    Access to the best<br>deals</div>
  <div class="feature" style="left:488px">
    <svg width="58" height="58" viewBox="0 0 58 58" fill="none" stroke="var(--icon)" stroke-width="2.5"><rect x="3" y="3" width="52" height="52" rx="6"/><path d="M17 41l3-10 18-18 7 7-18 18zM20 31l7 7"/></svg>
    Electronic offerings<br>and orderings</div>
  <div class="feature" style="left:700px">
    <svg width="70" height="58" viewBox="0 0 70 58" fill="none" stroke="var(--icon)" stroke-width="2.5"><rect x="12" y="8" width="46" height="32" rx="2"/><path d="M3 46h64l-4 6H7z"/></svg>
    Transaction status<br>monitoring</div>
  <div class="feature" style="left:937px">
    <svg width="58" height="58" viewBox="0 0 58 58" fill="none" stroke="var(--icon)" stroke-width="2.5"><path d="M10 6h38v24c0 12-9 20-19 24C19 50 10 42 10 30z"/><path d="M29 6v48"/></svg>
    Data and transaction<br>security</div>
</section>

<section class="how">
  <div class="abs tablet">
    <div class="screen" style="left:28px;top:18px;width:428px;height:304px;background:#eef0f3">
      <div class="side" style="width:62px"><div style="width:28px;height:28px;border-radius:50%;background:#c9ccd2;margin:22px auto"></div></div>
      <svg class="abs" style="left:74px;top:20px" width="340" height="170" viewBox="0 0 340 170" role="img" aria-label="Price area chart">
        <rect width="340" height="170" fill="#fff"/>
        <path d="M0 150 L30 140 L60 110 L90 60 L110 95 L130 130 L160 140 L190 70 L215 30 L240 100 L270 140 L300 120 L340 135 V170 H0Z" fill="#5a9e3a" opacity=".85"/>
        <path d="M0 160 L40 150 L80 120 L120 150 L170 120 L210 90 L250 140 L300 145 L340 150 V170 H0Z" fill="#3e8da8" opacity=".7"/>
      </svg>
      <div style="position:absolute;left:74px;top:205px;right:14px"><div class="row" style="background:#fff"></div><div class="row" style="background:#fff"></div><div class="row" style="background:#fff"></div><div class="row" style="background:#fff"></div></div>
    </div>
    <svg class="abs" style="left:200px;top:130px" width="74" height="74" viewBox="0 0 74 74"><circle cx="37" cy="37" r="33" fill="rgba(0,0,0,.35)" stroke="#fff" stroke-width="5"/><path d="M29 22l24 15-24 15z" fill="#fff"/></svg>
    <div class="abs" style="left:470px;top:160px;width:10px;height:10px;border-radius:50%;background:#555"></div>
  </div>
  <h2>How it Works</h2>
  <p>Aliquam molestie, mi et imperdiet euismod, dui purus auctor tellus, et interdum lacus lectus et ante. Sed accumsan sollicitudin sapien, sit amet adipiscing turpis gravida ac. In congue, neque ac lobortis volutpat, libero mauris varius mi, vitae suscipit ipsum ligula vitae risus.</p>
  <a class="abs btn" href="#">SEE HOW IT WORKS</a>
</section>

<section class="benefits purchaser">
  <h2 class="abs" style="left:74px;top:62px">Benefits for Oil Purchaser</h2>
  <ul class="benefit-list" style="left:78px;top:142px">
    <li><svg width="30" height="24" viewBox="0 0 30 24" fill="none" stroke="var(--orange)" stroke-width="2.5"><circle cx="8" cy="8" r="6"/><path d="M12 12l12 10M20 18l3-3M23 21l3-3"/></svg>Access to cheaper oil</li>
    <li><svg width="30" height="24" viewBox="0 0 30 24" fill="none" stroke="var(--orange)" stroke-width="2.5"><rect x="2" y="4" width="20" height="18" rx="2"/><path d="M10 16l2-5 10-9 3 3-10 9z"/></svg>Convenience of online orders</li>
    <li><svg width="30" height="24" viewBox="0 0 30 24" fill="none" stroke="var(--orange)" stroke-width="2.5"><path d="M3 8h22M19 3l6 5-6 5M27 17H5M11 12l-6 5 6 5"/></svg>Possibility to compare prices on the market</li>
    <li><svg width="30" height="24" viewBox="0 0 30 24" fill="none" stroke="var(--orange)" stroke-width="2.5"><circle cx="13" cy="12" r="10"/><path d="M13 6v6h5"/></svg>Transaction history</li>
    <li><svg width="30" height="24" viewBox="0 0 30 24" fill="none" stroke="var(--orange)" stroke-width="2.5"><rect x="5" y="3" width="20" height="14"/><path d="M1 20h28"/></svg>Order status monitoring</li>
    <li><svg width="30" height="24" viewBox="0 0 30 24" fill="var(--orange)"><path d="M4 1h20v11c0 6-5 10-10 12C9 22 4 18 4 12z"/></svg>Security and transparency of purchase</li>
  </ul>
  <div class="photo" style="left:613px;width:587px;background:linear-gradient(180deg,#2f5fa8 0%,#6a8fc4 40%,#c9a24a 65%,#3a3a3a 100%)" role="img" aria-label="Photo of a fuel station with a yellow canopy at dusk"></div>
</section>

<section class="benefits seller">
  <div class="photo" style="left:0;width:587px;background:linear-gradient(180deg,#6d7f9a 0%,#c9a96a 35%,#e8b24c 55%,#8a5a22 80%,#2a2320 100%)" role="img" aria-label="Photo of an illuminated oil refinery at sunset"></div>
  <h2 class="abs" style="left:635px;top:85px">Benefits for Oil Seller</h2>
  <ul class="benefit-list" style="left:650px;top:157px;width:430px">
    <li><svg width="30" height="24" viewBox="0 0 30 24" fill="var(--orange)"><rect x="11" y="1" width="8" height="7"/><rect x="1" y="16" width="8" height="7"/><rect x="11" y="16" width="8" height="7"/><rect x="21" y="16" width="8" height="7"/><path d="M14 8h2v4h9v4h-2v-2H7v2H5v-4h9z"/></svg>New sale channel</li>
    <li><svg width="30" height="24" viewBox="0 0 30 24" fill="var(--orange)"><circle cx="15" cy="6" r="5"/><circle cx="5" cy="8" r="4"/><circle cx="25" cy="8" r="4"/><path d="M6 24c0-7 4-11 9-11s9 4 9 11zM0 22c0-5 2-8 5-8 2 0 3 1 3 1l-3 7zM30 22c0-5-2-8-5-8-2 0-3 1-3 1l3 7z"/></svg>Attracting new clients</li>
    <li><svg width="30" height="24" viewBox="0 0 30 24" fill="var(--orange)"><path d="M15 1C11 8 7 12 7 16a8 8 0 0016 0c0-4-4-8-8-15z"/></svg>More oil sold</li>
    <li><svg width="30" height="24" viewBox="0 0 30 24" fill="var(--orange)"><path d="M9 10V7a6 6 0 0112 0v3h-3V7a3 3 0 00-6 0v3z"/><rect x="6" y="10" width="18" height="13" rx="2"/></svg>Transaction security</li>
    <li><svg width="30" height="28" viewBox="0 0 30 28" fill="none" stroke="var(--orange)" stroke-width="3"><circle cx="10" cy="17" r="6"/><circle cx="22" cy="7" r="4"/><path d="M10 7v3M10 24v3M0 17h3M17 17h3M22 0v2M22 12v2M15 7h2M27 7h2"/></svg>Possibility to integrate with distribution infrastructure and logistits for more efficient automation.</li>
  </ul>
</section>

<section class="contact">
  <h2>Contact Us</h2>
  <p class="sub">Vestibulum vel metus sit amet turpis bibendum tincidunt vel sit amet quam</p>
  <div class="field" style="left:164px;top:191px;width:423px;height:48px">Name</div>
  <div class="field" style="left:164px;top:246px;width:423px;height:48px">Email Address</div>
  <div class="field" style="left:164px;top:300px;width:423px;height:48px">Phone No</div>
  <div class="field" style="left:613px;top:191px;width:423px;height:157px">Message</div>
  <a class="abs btn" href="#">SEE HOW IT WORKS</a>
</section>

<footer class="footer">
  <div class="abs brand"><span class="brand-dot"></span>Oilvane</div>
  <div class="abs address">
    4410 Calder<br>Lane,Brennock, K17 42PT
    <div class="contact-line" style="margin-top:10px"><svg width="14" height="12" viewBox="0 0 14 12"><rect width="14" height="12" fill="var(--orange)"/><path d="M0 1l7 5 7-5" stroke="#fff" fill="none"/></svg>hello@oilvane-trade.com</div>
    <div class="contact-line" style="margin-top:6px"><svg width="14" height="16" viewBox="0 0 14 16"><path d="M7 0a6 6 0 00-6 6c0 5 6 10 6 10s6-5 6-10a6 6 0 00-6-6z" fill="var(--orange)"/><circle cx="7" cy="6" r="2" fill="#fff"/></svg>Map Location</div>
  </div>
  <div class="abs socials"><span></span><span></span><span></span><span></span><span></span><span></span></div>
  <div class="abs" style="left:379px;top:60px"><h4>SITE MAP</h4><ul><li>Home</li><li>About Us</li><li>Services</li><li>How it Works</li><li>Benefits</li><li>Blog</li><li>Contact Us</li></ul></div>
  <div class="abs" style="left:618px;top:60px"><h4>RESOURCES</h4><ul><li>Aliquam molestie</li><li>Perdiet euismod</li><li>Dui purus auctor tellus</li><li>Dum lacus lectus</li></ul></div>
  <div class="abs" style="left:883px;top:60px"><h4>NEWSLETTER SIGN UP</h4><div class="newsletter-input">Enter Email Address</div><a class="btn" href="#">SIGN UP</a></div>
  <div class="abs divider"></div>
  <p class="abs copyright">Copyright © 2017. Company Name. All Right Reserved</p>
</footer>

</body>
</html>
```